RWT Fittings Ltd Business Cards

We need a business card with our business logo. We provide window and door installations on high-rises in west coast British Colombia, Canada.

I would like my business information and details on one side of the card, and the other side the company name with logo

Target Market(s)

General Contractors

Industry/Entity Type

Construction

Contact Information for Business Card

one side i want my company name and logo in the dark theme logo that i provided

Requirements
Must have
• Marco Peltieri, 16045518293, RWTFittings@mailbox-demo.com, 1407-5194 Linden Row Burnaby BC, V5H 2K9, Owner & Manager

```html
<!DOCTYPE html>
<html lang="en">
<head>
<meta charset="utf-8">
<title>RWT Fittings Ltd Business Cards</title>
<link rel="stylesheet" href="https://fonts.googleapis.com/css2?family=Open+Sans:wght@400;600;700&display=swap">
<style>
  :root {
    --backdrop: #3a3a3a;
    --card: #161616;
    --accent: #29a9e1;
    --text-light: #f2f2f2;
    --text-muted: #cfcfcf;
  }
  * { box-sizing: border-box; margin: 0; padding: 0; }
  html, body {
    width: 1200px;
    height: 780px;
    overflow: hidden;
  }
  body {
    background: var(--backdrop);
    font-family: "Open Sans", Arial, sans-serif;
    display: flex;
    align-items: center;
    justify-content: center;
    gap: 40px;
  }
  .card {
    position: relative;
    width: 540px;
    height: 310px;
    background: var(--card);
    overflow: hidden;
  }

  /* Contact side */
  .wordmark {
    color: var(--accent);
    font-weight: 700;
    letter-spacing: 0.5px;
    line-height: 1;
    white-space: nowrap;
  }
  .card--contact .wordmark {
    position: absolute;
    top: 52px;
    left: 250px;
    font-size: 28px;
  }
  .identity {
    position: absolute;
    top: 144px;
    left: 30px;
    width: 190px;
  }
  .identity__name {
    color: var(--accent);
    font-weight: 700;
    font-size: 18px;
    letter-spacing: 0.3px;
    line-height: 1.2;
    white-space: nowrap;
  }
  .identity__title {
    color: var(--text-muted);
    font-size: 14px;
    margin-top: 4px;
    white-space: nowrap;
  }
  .divider {
    position: absolute;
    left: 226px;
    top: 124px;
    width: 1px;
    height: 96px;
    background: linear-gradient(to bottom, transparent, var(--accent), transparent);
  }
  .contacts {
    position: absolute;
    top: 130px;
    left: 242px;
    list-style: none;
  }
  .contacts li {
    display: flex;
    align-items: center;
    gap: 8px;
    color: var(--text-light);
    font-size: 15px;
    line-height: 27px;
    white-space: nowrap;
  }
  .contacts svg {
    width: 13px;
    height: 13px;
    fill: var(--accent);
    flex: none;
  }
  .address-band {
    position: absolute;
    left: 0;
    right: 0;
    bottom: 30px;
    height: 30px;
  }
  .address-band__bar {
    position: absolute;
    top: 0;
    height: 30px;
    background: var(--accent);
  }
  .address-band__bar--left { left: 0; width: 362px; }
  .address-band__bar--right { left: 402px; right: 0; }
  .address-band__text {
    position: absolute;
    left: 30px;
    top: 0;
    line-height: 30px;
    color: #ffffff;
    font-size: 13.5px;
    white-space: nowrap;
  }
  .address-band__square {
    position: absolute;
    left: 370px;
    top: 3px;
    width: 24px;
    height: 24px;
    background: var(--accent);
  }

  /* Brand side */
  .card--brand {
    display: flex;
    align-items: center;
    justify-content: center;
    gap: 16px;
  }
  .card--brand .brand-square {
    width: 46px;
    height: 46px;
    background: var(--accent);
  }
  .card--brand .wordmark {
    font-size: 44px;
  }
</style>
</head>
<body>

  <section class="card card--contact" aria-label="Contact side">
    <div class="wordmark">RWT Fittings Ltd</div>

    <div class="identity">
      <div class="identity__name">MARCO PELTIERI</div>
      <div class="identity__title">Owner &amp; Manager</div>
    </div>

    <div class="divider"></div>

    <ul class="contacts">
      <li>
        <svg viewBox="0 0 24 24" aria-hidden="true"><path d="M6.6 10.8a15.1 15.1 0 0 0 6.6 6.6l2.2-2.2a1 1 0 0 1 1-.25 11.4 11.4 0 0 0 3.6.57 1 1 0 0 1 1 1V20a1 1 0 0 1-1 1A17 17 0 0 1 3 4a1 1 0 0 1 1-1h3.5a1 1 0 0 1 1 1c0 1.25.2 2.45.57 3.57a1 1 0 0 1-.25 1z"/></svg>
        16045518293
      </li>
      <li>
        <svg viewBox="0 0 24 24" aria-hidden="true"><path d="M2 5h20v14H2z M2 5l10 8 10-8" fill="none" stroke="#29a9e1" stroke-width="2.4"/></svg>
        RWTFittings@mailbox-demo.com
      </li>
      <li>
        <svg viewBox="0 0 24 24" aria-hidden="true"><circle cx="12" cy="12" r="10"/></svg>
        www.rwtfittings-demo.com
      </li>
    </ul>

    <div class="address-band">
      <div class="address-band__bar address-band__bar--left"></div>
      <div class="address-band__square"></div>
      <div class="address-band__bar address-band__bar--right"></div>
      <div class="address-band__text">1407-5194 Linden Row Burnaby BC, V5H 2K9</div>
    </div>
  </section>

  <section class="card card--brand" aria-label="Brand side">
    <div class="brand-square"></div>
    <div class="wordmark">RWT Fittings Ltd</div>
  </section>

</body>
</html>
```